Brookvane Consulting Business Card Design

Business Card Design for Brookvane Consulting. Brookvane Consulting is a boutique consultancy based in Atlanta, GA., that specializes in marketing strategy, organization planning, and leadership development. We provide solutions for small businesses and startups as well as Vantage 300 companies.

http://brookvaneconsulting.com/

Target Market(s)

We provide solutions for small businesses and startups as well as Vantage 300 companies.

Industry/Entity Type

Consulting

Contact Information for Business Card

Two sided business card with priority on contact information, logo, tag line (Guidance to Plan Well, Lead Well, Grow Well)

Colors

Designer to choose colors to be used in the design.

Requirements
Must have
• contact information, logo, tag line (Guidance to Plan Well, Lead Well, Grow Well)
• Simple no over communication.
Nice to have
• I would like to see different placements of logo and creative use of both sides of the card
Should not have
• Do not put too much information on the card.

```html
<!DOCTYPE html>
<html lang="en">
<head>
<meta charset="utf-8">
<title>Brookvane Consulting – Business Card</title>
<link href="https://fonts.googleapis.com/css2?family=Montserrat:wght@400;600&family=Roboto:wght@400;700&display=swap" rel="stylesheet">
<style>
  :root {
    --backdrop: #5a5a5a;
    --card: #333333;
    --card-deep: #0d0d0d;
    --stripe: #8e8e8e;
    --ink: #ffffff;
  }
  * { margin: 0; padding: 0; box-sizing: border-box; }
  html, body { width: 799px; height: 1200px; overflow: hidden; }
  body {
    background: var(--backdrop);
    display: flex;
    flex-direction: column;
    align-items: center;
    justify-content: center;
    gap: 110px;
    font-family: "Roboto", sans-serif;
    color: var(--ink);
  }
  .card {
    position: relative;
    width: 620px;
    height: 354px;
    border-radius: 26px;
    background: var(--card);
    overflow: hidden;
  }
  .wordmark {
    font-family: "Montserrat", sans-serif;
    font-weight: 600;
    color: var(--ink);
    display: flex;
    align-items: center;
    gap: 14px;
    white-space: nowrap;
  }
  .wordmark-square {
    width: 18px;
    height: 18px;
    background: var(--ink);
    flex: none;
  }
  .card-front .wordmark {
    position: absolute;
    left: 50%;
    top: 50%;
    transform: translate(-50%, -50%);
    font-size: 40px;
  }
  .card-back .wordmark {
    position: absolute;
    left: 34px;
    top: 30px;
    font-size: 30px;
  }
  .card-back .wordmark-square { width: 14px; height: 14px; }
  .wave {
    position: absolute;
    inset: 0;
    width: 100%;
    height: 100%;
  }
  .contact {
    position: absolute;
    left: 34px;
    top: 92px;
    font-size: 14px;
    line-height: 1.35;
  }
  .contact-name {
    font-family: "Montserrat", sans-serif;
    font-weight: 600;
    font-size: 19px;
    margin-bottom: 8px;
  }
  .tagline {
    position: absolute;
    right: 34px;
    bottom: 18px;
    text-align: right;
    font-size: 15px;
    line-height: 1.25;
  }
</style>
</head>
<body>

  <section class="card card-front" aria-label="Card front">
    <div class="wordmark"><span class="wordmark-square"></span>Brookvane Consulting</div>
  </section>

  <section class="card card-back" aria-label="Card back">
    <svg class="wave" viewBox="0 0 620 354" preserveAspectRatio="none" aria-hidden="true">
      <path d="M0 205 C 100 225, 200 262, 330 254 S 540 212, 620 212 L620 354 L0 354 Z" fill="var(--stripe)"/>
      <path d="M0 215 C 100 235, 200 272, 330 264 S 540 222, 620 222 L620 354 L0 354 Z" fill="var(--card)"/>
      <path d="M0 227 C 100 247, 200 284, 330 276 S 540 234, 620 234 L620 354 L0 354 Z" fill="var(--stripe)"/>
      <path d="M0 237 C 100 257, 200 294, 330 286 S 540 244, 620 244 L620 354 L0 354 Z" fill="var(--card-deep)"/>
    </svg>
    <div class="wordmark"><span class="wordmark-square"></span>Brookvane Consulting</div>
    <div class="contact">
      <p class="contact-name">Dario</p>
      <p>555-014-2297</p>
      <p>dario@brookvaneconsulting.com</p>
      <p>www.brookvaneconsulting.com</p>
    </div>
    <p class="tagline">Guidance to<br>Plan Well,<br>Lead Well,<br>Grow Well</p>
  </section>

</body>
</html>
```